Specialised investor in e-mobility and energy wants business card design

We need a business card design that fits our existing corporate design. <The look and feel must be 'sharp'/'clean', dynamic, communicate momentum, professionalism etc (as one would imagine from a firm in the financial sector). We like the idea of a reverse-side of the card that includes the logo, and the name and contact details on the other. We expect the deliverable to be whatever format might be required to be able to get cards printed directly by a service such as kelmo press. Our website is www.zub.capital

```html
<!DOCTYPE html>
<html lang="en">
<head>
<meta charset="utf-8">
<title>Zub Capital – Business Card</title>
<link href="https://fonts.googleapis.com/css2?family=Montserrat:wght@400;500;700;800&display=swap" rel="stylesheet">
<style>
  :root{
    --bg:#d3d6d5;
    --card:#f5f5f3;
    --green-dark:#1f4a1c;
    --green-light:#6aa531;
    --ink:#3b3b3b;
    --rule:#4d5a4a;
  }
  *{box-sizing:border-box;margin:0;padding:0}
  html,body{width:1200px;height:905px;overflow:hidden;background:var(--bg)}
  body{font-family:'Montserrat',sans-serif;color:var(--ink);position:relative}
  .card{
    position:absolute;left:250px;width:700px;height:400px;
    background:var(--card);
    box-shadow:0 6px 18px rgba(0,0,0,.12);
  }
  .card--front{top:32px;border-bottom:5px solid var(--green-light)}
  .card--back{top:472px}

  .wordmark{
    display:flex;align-items:center;justify-content:center;gap:14px;
    color:var(--green-dark);font-weight:500;
  }
  .wordmark__dot{border-radius:50%;background:var(--green-dark);flex:none}
  .card--front .wordmark{margin-top:62px;font-size:50px}
  .card--front .wordmark__dot{width:20px;height:20px}
  .card--back .wordmark{height:100%;font-size:76px}
  .card--back .wordmark__dot{width:28px;height:28px}

  .person{text-align:center;margin-top:34px}
  .person__name{font-size:26px;font-weight:800;letter-spacing:1px;color:var(--green-dark)}
  .person__name span{color:var(--green-light)}
  .person__role{font-size:15px;margin-top:2px;color:var(--ink)}

  .details{display:flex;justify-content:center;margin-top:26px}
  .details__address{
    text-align:right;font-size:15px;line-height:1.55;padding-right:22px;
    border-right:1.5px solid var(--rule);padding-top:2px;
  }
  .details__contact{list-style:none;padding-left:22px;font-size:15px;line-height:1.55}
  .details__contact li{display:flex;align-items:center;gap:9px}
  .details__contact svg{width:13px;height:13px;fill:var(--green-light);flex:none}
</style>
</head>
<body>

<section class="card card--front" aria-label="Card front">
  <div class="wordmark"><span class="wordmark__dot"></span><span>Zub Capital</span></div>

  <div class="person">
    <p class="person__name">MARTEN <span>OLBY</span></p>
    <p class="person__role">Director/Founder</p>
  </div>

  <div class="details">
    <address class="details__address" style="font-style:normal">
      1234 Street Name<br>Country Name AB 5748
    </address>
    <ul class="details__contact">
      <li>
        <svg viewBox="0 0 24 24"><path d="M6.6 10.8a15.1 15.1 0 0 0 6.6 6.6l2.2-2.2a1 1 0 0 1 1-.25 11.4 11.4 0 0 0 3.6.57 1 1 0 0 1 1 1V20a1 1 0 0 1-1 1A17 17 0 0 1 3 4a1 1 0 0 1 1-1h3.5a1 1 0 0 1 1 1c0 1.25.2 2.45.57 3.57a1 1 0 0 1-.25 1z"/></svg>
        123-408-2291
      </li>
      <li>
        <svg viewBox="0 0 24 24"><path d="M2 5h20v2l-10 6L2 7z"/><path d="M2 9l10 6 10-6v10H2z"/></svg>
        info@zub.capital
      </li>
      <li>
        <svg viewBox="0 0 24 24"><circle cx="12" cy="12" r="10"/><path d="M2 12h20M12 2c3 3 3 17 0 20M12 2c-3 3-3 17 0 20" stroke="#f5f5f3" stroke-width="1.5" fill="none"/></svg>
        www.zub.capital
      </li>
    </ul>
  </div>
</section>

<section class="card card--back" aria-label="Card back">
  <div class="wordmark"><span class="wordmark__dot"></span><span>Zub Capital</span></div>
</section>

</body>
</html>
```